Systems and Technology Consultants - Website

Design & Build a website for a new company which operates in the Systems and Technology space for Transportation, Government and Commercial sectors.

Overall design should be minimalist in nature.
Should also have a feed that provides news and event updates on the main page.
Logo has already been awarded and should be incorporated into the site.

We like the overall layout, functionality and simplicity of the below sites. Submitted designs could be similar to or a combination of the aspects on these sites, or perhaps a whole different concept - we are open to new ideas.
Norvique.com
Teblo.it

Update 1 Dated 27 May 2014

All I am moving away from the Teblo.it website and would like it to be more aligned with Norvique.com not only in layout but in functionality. I will be extending the deadline of this design brief for two weeks to incorporate additional requirements and will add addtional funding to the project.

Apologies for not having more information available to provide but with so many submissions its getting confusing.

Thanks Derek

Please note that the brief has been updated and the deadline has been extended.

Important: We will need two language versions of the website, English and Arabic; the website is hosted on HostPelican

Hello All, Thank you for your submissions. We have narrowed it down to the final 6 designers and I just wanted to take a moment and provide a bit of feedback regarding the concepts that we like and the modifications we are looking for. First, let me mention some of the design functions we like. - At the top of the homepage we really like the "region" or "language" tab so that the website can be viewed in both English and Arabic. - We like the homepage to have clear color variation so that the different sections of the homepage are distinct. Additionally, we like the bottom portion of the homepage to be in red. We feel that draws attention to our contact information. Again, we would like the colors to integrate black, gray-scale, red, etc. - Having a search tab at the top of the home page, or integrated into the main image, so that the site is easy to navigate. - We especially like the main image to have the scrolling tabs at the bottom so it is easy to browse the services offered (Consultancy, Solutions Architecture, Masters Systems Integration, Independent Design Review). - In regards to the services offered tab we really like the idea that a few people presented that have the outside of our logo with an icon in the middle of consultancy, solutions, etc., etc. Secondly, as mentioned in our brief we really enjoy the design of norvique site. Specially, we enjoy the strong iconic images they use, the way the tabs at the top scroll easily, and contact us page that generates an email. Lastly, I've included some photos of the concept we have been working on. What we are trying to demonstrate is how our company offers a range of services that are essentially linked together. We provide individual services that when combined present the full service package. We would like this concept to be integrated into the over concept of our website. Please feel free to ask for clarification of any of the above points or contact us if you have any additional questions. We appreciate all of your hard work and are very excited to see the updated designs. Best, Marta Vennick Quelbrant Senior Program Manager marta.vennick@quelbrant-example.com

Industry/Entity Type

Government

Font styles to use
Serif
Sans Serif

Requirements
Must have
• Must work on/adapt to various/mobile devices (responsive)
Must be simple and straightforward
Colors should be in line/matching with logo
2 language versions: English and Arabic (no Thai)
Services should be the first group/row of items after/below the main image
Note: the website will be hosted by hostpelican
Nice to have
• Submit feedback form
What's New section
The banner at the bottom of the site should not be too large; we would like a narrow one more
It would be nice if the header/top banner (with Home, About, etc. tabs) could stay in place as you scroll down (like Norvique and Chatterloop)
We will likely only use one image with a Company slogan on the Home page rather than a carousel of images to rotate through
Should not have
• This is the existing website: http://www.quelbrant-example.org
We do not like the animation, the way the banner icons/titles bounce
Not simple enough, we don't like the functionality or how pages load so slowly
We do not like the logo centered - it should be at the left
The banner and its tabs should not be towards the right, we would like them to be centered, to go all the way across and to be below the logo

```html
<!DOCTYPE html>
<html lang="en">
<head>
<meta charset="utf-8">
<title>Quelbrant – Home</title>
<link href="https://fonts.googleapis.com/css2?family=ABeeZee&family=Play:wght@400;700&family=Ubuntu:wght@400;500&display=swap" rel="stylesheet">
<style>
:root{
  --red:#e31e25;
  --red-dark:#c8151b;
  --white:#ffffff;
  --ink:#555555;
  --muted:#a6a6a6;
  --line:#e3e3e3;
  --footer:#333333;
  --hero-a:#b8404f;
  --hero-b:#d8707c;
}
*{margin:0;padding:0;box-sizing:border-box}
html,body{width:1200px;height:1200px;overflow:hidden;background:var(--white)}
body{position:relative;font-family:"ABeeZee",sans-serif;color:var(--ink)}
.abs{position:absolute}

/* header */
.site-header{left:0;top:0;width:1200px;height:49px;background:var(--white);border-bottom:3px solid var(--red)}
.brand{left:187px;top:12px;display:flex;align-items:center;gap:8px}
.brand-mark{width:20px;height:20px;border-radius:50%;background:var(--red)}
.brand-name{font-family:"Play",sans-serif;font-weight:700;font-size:19px;letter-spacing:4px;color:var(--red)}
.main-nav{left:445px;top:18px;display:flex;gap:0;font-family:"Ubuntu",sans-serif;font-size:13px;color:var(--muted)}
.main-nav span{margin-right:29px}
.main-nav .active{color:var(--red);font-weight:500}
.social-top{left:952px;top:16px;display:flex;gap:7px}
.social-top span{width:18px;height:18px;border-radius:50%;background:#d4d4d4}
.social-top span:first-child{background:var(--red)}

/* hero */
.hero{left:0;top:49px;width:1200px;height:369px;background:linear-gradient(100deg,#d7a0a7 0%,var(--hero-b) 35%,var(--hero-a) 70%,#d4919a 100%)}
.hero-slogan{left:205px;top:203px;width:390px;font-family:"Play",sans-serif;font-size:16px;line-height:18px;color:var(--white)}
.hero-badge{left:626px;top:170px;width:128px;height:128px;border-radius:50%;background:var(--white);box-shadow:0 0 40px 16px rgba(255,120,170,.55)}
.hero-name{left:790px;top:212px;font-family:"Play",sans-serif;font-weight:700;font-size:28px;letter-spacing:8px;color:var(--white)}
.hero-dots{left:857px;top:264px;display:flex;gap:6px}
.hero-dots span{width:11px;height:11px;border-radius:50%;background:var(--white)}
.hero-dots .current{background:var(--red);border:2px solid var(--white)}

/* welcome */
.section-title{font-family:"Play",sans-serif;font-size:25px;color:var(--red)}
.welcome-title{left:197px;top:458px}
.welcome-text{left:198px;top:493px;width:385px;font-size:12.2px;line-height:14.5px;color:#666}
.welcome-text p{margin-bottom:14px}
.divider{left:598px;top:497px;width:1px;height:268px;background:var(--line)}

/* services */
.services-title{left:620px;top:458px}
.service{width:127px;height:121px;border:1px solid var(--line);display:flex;flex-direction:column;align-items:center;justify-content:flex-end;padding-bottom:30px;font-family:"Ubuntu",sans-serif;font-size:10.5px;color:var(--muted);background:var(--white)}
.service svg{margin-bottom:10px}
.service.selected{border:1px solid var(--red);color:var(--red);font-weight:500;font-size:12px;box-shadow:0 0 4px rgba(0,0,0,.15)}

/* red band */
.info-band{left:0;top:828px;width:1200px;height:310px;background:var(--red)}
.col-title{font-family:"Ubuntu",sans-serif;font-weight:500;font-size:15px;color:var(--white);border-bottom:1px solid rgba(255,255,255,.8);padding-bottom:7px;display:flex;justify-content:space-between;align-items:center}
.col-title i{width:16px;height:14px;border:2px solid var(--white);border-radius:2px;display:block}
.small{font-size:9.5px;line-height:12px;color:var(--white)}
.item-head{font-family:"Ubuntu",sans-serif;font-size:11px;font-weight:500;color:var(--white)}
.news-thumb{width:56px;height:46px}
.rule{height:1px;background:rgba(255,255,255,.8)}
.link{font-family:"Ubuntu",sans-serif;font-size:11px;color:var(--white);text-align:right}
.contact-name{font-family:"Play",sans-serif;font-weight:700;font-size:15px;letter-spacing:5px;color:var(--white);display:flex;align-items:center;gap:8px}
.contact-name b{width:18px;height:18px;border-radius:50%;border:2px solid var(--white);display:block}
.social-foot{display:flex;gap:6px}
.social-foot span{width:19px;height:19px;border-radius:50%;background:var(--white)}
.social-foot span:last-child{background:transparent;border:1px solid var(--red-dark)}

/* footer */
.site-footer{left:0;top:1138px;width:1200px;height:62px;background:var(--footer)}
.copyright{left:192px;top:1163px;font-family:"Ubuntu",sans-serif;font-size:9.5px;color:#aaa}
.share-count{left:940px;top:1161px;display:flex;gap:4px;align-items:center}
.share-count span:first-child{width:28px;height:17px;background:#eee;border-radius:2px}
.share-count span:last-child{font-size:9px;color:#333;background:#f4f4f4;border-radius:3px;padding:2px 6px}
</style>
</head>
<body>

<header class="site-header abs">
</header>
<div class="brand abs"><span class="brand-mark"></span><span class="brand-name">QUELBRANT</span></div>
<nav class="main-nav abs">
  <span class="active">Home</span><span>Business Unit</span><span>Services ▾</span><span>About Us</span><span>Locations</span><span>Contact Us</span>
</nav>
<div class="social-top abs"><span></span><span></span><span></span></div>

<section class="hero abs" role="img" aria-label="Businesswoman seated before a red-tinted digital dashboard with charts, calendar and world map"></section>
<p class="hero-slogan abs">Quelbrant Int. specializes in delivering quality professional services and technical projects that support larger business goals.</p>
<div class="hero-badge abs"></div>
<div class="hero-name abs">QUELBRANT</div>
<div class="hero-dots abs"><span></span><span class="current"></span><span></span><span></span></div>

<h2 class="section-title welcome-title abs">Welcome</h2>
<div class="welcome-text abs">
  <p>Quelbrant specializes in delivering quality professional services and technical projects that support larger business goals. systems are tools that support a greater business function and need. we understand that most technical projects are conceptualized to support a larger vision with actual business goals in mind and ensure that all of our professional and certified expertise is included in our professional services to meet those goals.</p>
  <p>quelbrant recognizes the middle east and greater asia regions are economic growth markets with developing infrastructure projects requiring specialist systems and technical expertise. accordingly, quelbrant has evolved its presence in the regions to meet client demands and expectations.</p>
  <p>our ultimate goal is to provide quality, technical and professional services on projects of any scale and/or complexity, from conception through to completion. our philosophy is simple; stick to what you are good at and be the best at it.</p>
</div>
<div class="divider abs"></div>

<h2 class="section-title services-title abs">Services</h2>
<div class="service abs" style="left:621px;top:497px">
  <svg width="36" height="34" viewBox="0 0 36 34" fill="#a9a9a9"><circle cx="8" cy="6" r="4"/><circle cx="18" cy="6" r="4"/><circle cx="28" cy="6" r="4"/><rect x="3" y="12" width="30" height="6"/><rect x="5" y="18" width="4" height="14"/><rect x="27" y="18" width="4" height="14"/><rect x="14" y="20" width="8" height="10"/></svg>
  CONSULTING
</div>
<div class="service selected abs" style="left:753px;top:497px">
  <svg width="44" height="38" viewBox="0 0 44 38" fill="#e31e25"><rect x="16" y="0" width="12" height="7"/><rect x="8" y="9" width="28" height="8"/><rect x="2" y="19" width="40" height="8"/><rect x="2" y="29" width="22" height="8"/><path d="M26 37 L34 24 L42 37 Z"/></svg>
  ENGINEERING
</div>
<div class="service abs" style="left:885px;top:497px">
  <svg width="40" height="40" viewBox="0 0 40 40" fill="#a9a9a9"><circle cx="14" cy="26" r="11"/><circle cx="14" cy="26" r="4" fill="#fff"/><circle cx="31" cy="9" r="7"/><circle cx="31" cy="9" r="2.5" fill="#fff"/></svg>
  MAINTENANCE
</div>
<div class="service abs" style="left:621px;top:625px">
  <svg width="40" height="36" viewBox="0 0 40 36" fill="#a9a9a9"><circle cx="7" cy="6" r="4"/><rect x="3" y="11" width="8" height="16"/><rect x="3" y="27" width="3" height="9"/><rect x="8" y="27" width="3" height="9"/><rect x="15" y="3" width="23" height="20" fill="none" stroke="#a9a9a9" stroke-width="3"/><rect x="25" y="23" width="3" height="10"/></svg>
  OPERATIONS
</div>
<div class="service abs" style="left:753px;top:625px">
  <svg width="44" height="36" viewBox="0 0 44 36" fill="#a9a9a9"><rect x="28" y="0" width="10" height="6"/><rect x="2" y="8" width="18" height="7"/><rect x="22" y="8" width="20" height="7"/><rect x="2" y="17" width="10" height="7"/><rect x="14" y="17" width="16" height="7"/><rect x="32" y="17" width="10" height="7"/><rect x="2" y="26" width="18" height="7"/><rect x="22" y="26" width="20" height="7"/></svg>
  CONSTRUCTION
</div>

<section class="info-band abs"></section>

<!-- latest news -->
<div class="abs" style="left:195px;top:869px;width:237px"><div class="col-title">Latest News <i></i></div></div>
<div class="news-thumb abs" style="left:195px;top:904px;background:linear-gradient(180deg,#c9c4bd,#6f6760)" role="img" aria-label="Runner on a road"></div>
<div class="item-head abs" style="left:257px;top:903px">Lorem ipsum</div>
<div class="small abs" style="left:257px;top:917px;width:175px">Lorem ipsum dolor sit amet, consectetuer adipiscing elit, sed diam nonummy nibh euismod</div>
<div class="small abs" style="left:195px;top:954px;width:237px">tincidunt ut laoreet dolore magna aliquam erat volutpat.</div>
<div class="rule abs" style="left:195px;top:995px;width:237px"></div>
<div class="news-thumb abs" style="left:195px;top:1006px;background:var(--white);border:1px solid #ddd"></div>
<div class="item-head abs" style="left:257px;top:1006px">Duis autem vel</div>
<div class="small abs" style="left:257px;top:1020px;width:175px">Ut wisi enim ad minim veniam, quis nostrud exerci tation ullamcorper suscipit lobortis nisl</div>
<div class="small abs" style="left:195px;top:1057px;width:237px">ut aliquip ex ea commodo consequat.</div>
<div class="link abs" style="left:195px;top:1072px;width:237px">Read More...</div>
<div class="rule abs" style="left:195px;top:1093px;width:237px"></div>

<!-- events -->
<div class="abs" style="left:484px;top:869px;width:236px"><div class="col-title">Events <i></i></div></div>
<div class="item-head abs" style="left:486px;top:903px;width:236px;display:flex;justify-content:space-between"><span>Lorem ipsum</span><span>11-22-2014</span></div>
<div class="small abs" style="left:486px;top:917px;width:236px">Ut wisi enim ad minim veniam, quis nostrud exerci tation ullamcorper suscipit lobortis nisl ut aliquip ex ea commodo consequat.</div>
<div class="link abs" style="left:484px;top:974px;width:236px">Go to Event</div>
<div class="rule abs" style="left:484px;top:995px;width:236px"></div>
<div class="item-head abs" style="left:486px;top:1006px;width:236px;display:flex;justify-content:space-between"><span>Lorem ipsum</span><span>11-22-2014</span></div>
<div class="small abs" style="left:486px;top:1021px;width:248px">Duis autem vel eum iriure dolor in hendrerit in vulputate velit esse molestie consequat, vel illum dolore eu feugiat nulla facilisis at vero eros et accumsan ...</div>
<div class="link abs" style="left:484px;top:1072px;width:236px">Go to Event</div>
<div class="rule abs" style="left:484px;top:1093px;width:236px"></div>

<!-- contact -->
<div class="abs" style="left:771px;top:869px;width:236px"><div class="col-title">Contact Us <i></i></div></div>
<div class="contact-name abs" style="left:771px;top:904px"><b></b>QUELBRANT</div>
<div class="item-head abs" style="left:771px;top:936px">Main Office Bangkok Branch</div>
<div class="small abs" style="left:771px;top:951px;width:240px">address: 14 harrow lane, eastfield, bangkok 10990<br>phone numbers: +(66)-02-555-0147-8<br>email: info@quelbrant-example.org</div>
<div class="social-foot abs" style="left:769px;top:1008px"><span></span><span></span><span></span></div>

<footer class="site-footer abs"></footer>
<div class="copyright abs">Copyright 2005-2014 www.quelbrant-example.biz All rights reserved.</div>
<div class="share-count abs"><span></span><span>3,450</span></div>

</body>
</html>
```